Pet Sitting Business Card

Would like a business card designed for my new pet sitting business
Card needs to match with logo design.
Blue and Orange are the theme colours.

Simple yet sophisticated design

company name:- MEADOWLARK PET CARE
Dana Kovich
Owner
0452716093
dana@meadowlarkpetcare.com.au
www.meadowlarkpetcare.com.au

I'm going to close my deadline early. I will be picking a winner by the 10th of May. Please submit designs before then.
thank you

Target Market(s)

All types of professional pet lovers wishing to have their pet looked after

Industry/Entity Type

Pet

Requirements
Must have
• Logo design
Blue and orange

```html
<!DOCTYPE html>
<html lang="en">
<head>
<meta charset="utf-8">
<title>Meadowlark Pet Care – Business Card</title>
<link rel="stylesheet" href="https://fonts.googleapis.com/css2?family=Exo+2:wght@400;600;800&display=swap">
<style>
  :root {
    --blue: #1f8ef1;
    --blue-light: #5cc6d9;
    --orange: #ee8a2a;
    --ink: #1d1d1d;
    --card: #ffffff;
    --bg: #eceff2;
  }
  * { box-sizing: border-box; margin: 0; padding: 0; }
  html, body { width: 1200px; height: 905px; overflow: hidden; }
  body {
    background: var(--bg);
    font-family: "Exo 2", sans-serif;
    display: flex;
    align-items: center;
    justify-content: center;
    gap: 40px;
  }
  .card {
    position: relative;
    width: 540px;
    height: 320px;
    background: var(--card);
    box-shadow: 0 6px 18px rgba(0,0,0,0.12);
    overflow: hidden;
  }
  .brand {
    position: absolute;
    text-align: center;
  }
  .brand-name {
    font-weight: 800;
    color: var(--blue);
    letter-spacing: 1px;
    line-height: 1.05;
  }
  .brand-tagline {
    font-weight: 400;
    color: var(--blue);
    margin-top: 4px;
  }
  .card-front .brand {
    left: 0; right: 0; top: 50%;
    transform: translateY(-50%);
  }
  .card-front .brand-name { font-size: 34px; }
  .card-front .brand-tagline { font-size: 14px; }

  .card-back .swoosh { position: absolute; inset: 0; }
  .holder {
    position: absolute;
    left: 28px; top: 18px;
    color: #fff;
    text-transform: uppercase;
  }
  .holder-name { font-size: 19px; font-weight: 600; letter-spacing: 1px; }
  .holder-role { font-size: 12px; font-weight: 400; letter-spacing: 1px; margin-top: 2px; }
  .address {
    position: absolute;
    left: 28px; top: 108px;
    font-size: 13px;
    line-height: 1.35;
    color: var(--ink);
  }
  .contacts {
    position: absolute;
    left: 28px; top: 158px;
    list-style: none;
    font-size: 12px;
    color: var(--ink);
  }
  .contacts li { display: flex; align-items: center; gap: 8px; height: 22px; }
  .contacts svg { width: 13px; height: 13px; fill: var(--blue); flex: none; }
  .card-back .brand { right: 26px; bottom: 34px; }
  .card-back .brand-name { font-size: 24px; }
  .card-back .brand-tagline { font-size: 11px; }
</style>
</head>
<body>

<section class="card card-front" aria-label="Card front">
  <div class="brand">
    <div class="brand-name">MEADOWLARK<br>PET CARE</div>
    <div class="brand-tagline">Caring for the pets you love most</div>
  </div>
</section>

<section class="card card-back" aria-label="Card back">
  <svg class="swoosh" viewBox="0 0 540 320" preserveAspectRatio="none" aria-hidden="true">
    <defs>
      <linearGradient id="bandGradient" x1="0" y1="0" x2="1" y2="0.4">
        <stop offset="0" stop-color="#1f8ef1"/>
        <stop offset="0.6" stop-color="#5cc6d9"/>
        <stop offset="1" stop-color="#2f95ef"/>
      </linearGradient>
    </defs>
    <path d="M0,0 L260,0 C370,55 460,105 540,140 L540,162 C430,120 300,92 0,78 Z" fill="url(#bandGradient)"/>
    <path d="M170,106 C330,112 460,140 540,170 L540,184 C450,158 330,124 170,106 Z" fill="#ee8a2a"/>
  </svg>

  <div class="holder">
    <div class="holder-name">Dana Kovich</div>
    <div class="holder-role">Owner</div>
  </div>

  <div class="address">214, 6th floor, Harbour<br>Lane Road KTN</div>

  <ul class="contacts">
    <li><svg viewBox="0 0 24 24"><path d="M6.6 10.8a15.1 15.1 0 0 0 6.6 6.6l2.2-2.2c.3-.3.7-.4 1-.2 1.1.4 2.3.6 3.6.6.6 0 1 .4 1 1V20c0 .6-.4 1-1 1C10.6 21 3 13.4 3 4c0-.6.4-1 1-1h3.5c.6 0 1 .4 1 1 0 1.3.2 2.5.6 3.6.1.3 0 .7-.2 1z"/></svg>0452 716 093</li>
    <li><svg viewBox="0 0 24 24"><path d="M7 1h10a2 2 0 0 1 2 2v18a2 2 0 0 1-2 2H7a2 2 0 0 1-2-2V3a2 2 0 0 1 2-2zm0 3v14h10V4z"/></svg>0452 716 093</li>
    <li><svg viewBox="0 0 24 24"><path d="M3 5h18v14H3zm2 2v2l7 4 7-4V7l-7 4z"/></svg>dana@meadowlarkpetcare.com.au</li>
    <li><svg viewBox="0 0 24 24"><path d="M12 2a10 10 0 1 0 0 20 10 10 0 0 0 0-20zm6.9 9h-3a15 15 0 0 0-1.3-5.6A8 8 0 0 1 18.9 11zM12 4c.9 1.2 1.7 3.8 1.9 7h-3.8c.2-3.2 1-5.8 1.9-7zM9.4 5.4A15 15 0 0 0 8.1 11h-3a8 8 0 0 1 4.3-5.6zM5.1 13h3a15 15 0 0 0 1.3 5.6A8 8 0 0 1 5.1 13zM12 20c-.9-1.2-1.7-3.8-1.9-7h3.8c-.2 3.2-1 5.800-1.9 7zm2.6-1.4a15 15 0 0 0 1.3-5.6h3a8 8 0 0 1-4.3 5.6z"/></svg>www.meadowlarkpetcare.com.au</li>
  </ul>

  <div class="brand">
    <div class="brand-name">MEADOWLARK<br>PET CARE</div>
    <div class="brand-tagline">Caring for the pets you love most</div>
  </div>
</section>

</body>
</html>
```